Redesign of General Contractor Website

I currently have a wordpress site that needs some work. I would like to revitalize what we currently have to look more modern and up-to-date.
I want to be able to easily post pictures from new jobs and have a link to my own blog (not yet online). My current website can be found at www.brovikbuilders.com
the attached pictures are a site I built in Muse. i really like that sort of theme.
PLEASE NOTE: I am not interested in completely remaking the site, simply adding more functionalty and spicing it up a bit. (more animation, interactive elements, layering, etc...)
Target Market(s)
Property owners, Home owners, business owners, property managers, Decision makers purchasing a construction project, specifically Remodels, renovations, or damage restoration, with some or limited knowledge about how to complete one of those projects.
Industry/Entity Type
Contractor
Coding
Coded - Design and coding required
Number of Pages Required
1 page
Requirements
Must have
- Updateable photo bank displaying pictures from recent jobs that we can easily change and update. An embedded youtube pane showing our most recent video via our youtube channel. Animation and/or transition effects. The small circular logos must stay (I would like to see these be used with animation/transitional effects.
- Must be consistent with other marketing material. This can be found on our facebook page or in the power point file attached.
- Must use colors and fonts found at www.brovikbuilders.com
Nice to have
- Stock photos available if needed.
Should not have
- changes in logo design or re wording of text (use lorim ipsum if needed)
- No multiple pages, redesigning fonts

```html
<!DOCTYPE html>
<html lang="en">
<head>
<meta charset="utf-8">
<title>Brovik Contracting</title>
<link href="https://fonts.googleapis.com/css2?family=Roboto:wght@300;400;500;700;900&family=Roboto+Condensed:wght@400;700&display=swap" rel="stylesheet">
<style>
:root{
  --navy:#1f2d6e;
  --navy-deep:#172358;
  --orange:#e8491d;
  --grey:#efeded;
  --panel:#f4f4f4;
  --text:#333;
  --muted:#666;
  --white:#fff;
}
*{box-sizing:border-box;margin:0;padding:0}
html,body{width:1200px;height:4196px;overflow:hidden}
body{position:relative;font-family:"Roboto",Arial,sans-serif;color:var(--text);background:var(--white)}
.abs{position:absolute}
a{color:inherit;text-decoration:none}

/* header */
.topbar{left:0;top:0;width:1200px;height:84px;background:var(--navy)}
.topbar .call{right:110px;top:10px;color:#fff;text-align:left}
.topbar .call small{display:flex;align-items:center;gap:8px;font-size:13px}
.topbar .call strong{display:block;font-size:30px;font-weight:400;letter-spacing:.5px}
.navbar{left:0;top:84px;width:1200px;height:45px;background:var(--orange)}
.nav{left:248px;top:0;height:45px;display:flex;gap:40px;align-items:center;color:#fff;font-size:15px}
.social{display:flex;gap:10px}
.social span{width:30px;height:30px;border-radius:50%;display:block}
.navbar .social{right:120px;top:7px}
.social.blue span{background:#3b8fd8}
.brand-badge{left:104px;top:4px;width:120px;height:120px;border-radius:50%;background:#fff;box-shadow:0 3px 10px rgba(0,0,0,.3);display:flex;align-items:center;justify-content:center;color:var(--navy);font-weight:900;font-size:24px;letter-spacing:1px}

/* hero */
.hero{left:0;top:129px;width:1200px;height:491px;background:linear-gradient(100deg,#2d3640 0%,#56606a 45%,#7b6d5c 75%,#4a4f55 100%);clip-path:polygon(0 0,100% 0,100% 70%,0 100%)}
.hero-copy{left:162px;top:290px;width:440px;color:#fff}
.hero-copy h1{font-family:"Roboto Condensed",sans-serif;font-weight:400;font-size:44px;letter-spacing:.5px;line-height:1;white-space:nowrap}
.hero-copy h2{font-size:14px;font-weight:400;margin-top:8px}
.hero-copy p{font-size:14.5px;line-height:1.2;margin-top:4px}
.btn{display:inline-flex;align-items:center;justify-content:center;color:#fff;font-size:14px;font-weight:500}
.btn-learn{left:162px;top:462px;width:136px;height:36px;background:var(--navy);border-radius:3px;font-weight:700}
.badges{left:162px;top:535px;display:flex;gap:14px}
.badges span{display:block;height:40px;background:#fff;border-radius:3px}
.arrow-circle{width:38px;height:38px;border-radius:50%;background:rgba(255,255,255,.55);display:flex;align-items:center;justify-content:center}
.side-tab{left:0;top:362px;width:44px;height:168px;background:var(--orange);border-radius:0 6px 6px 0;color:#fff}
.side-tab span{position:absolute;left:10px;top:44px;writing-mode:vertical-rl;font-size:15px}

/* section titles */
.title{left:0;width:1200px;text-align:center;font-weight:700;font-size:27px;letter-spacing:.5px;color:#222}

/* our work */
.video{left:98px;top:772px;width:500px;height:296px;border:6px solid #fff;box-shadow:0 2px 10px rgba(0,0,0,.35);background:linear-gradient(160deg,#8f9296,#5d6166 60%,#7a7e7a)}
.play{left:290px;top:880px;width:64px;height:64px;border-radius:50%;background:#d8221b;display:flex;align-items:center;justify-content:center}
.team{left:638px;top:762px;width:434px}
.team h3{color:var(--orange);font-size:15px;font-weight:500;display:flex;align-items:center;gap:12px}
.team h3::after{content:"";flex:1;height:1px;background:#bbb}
.member{display:flex;gap:14px;margin-top:20px}
.member .ico{width:48px;height:48px;border-radius:50%;flex:none;border:1px solid #bbb;display:flex;align-items:center;justify-content:center}
.member .ico.on{background:var(--orange);border-color:var(--orange)}
.member b{font-size:13px;font-weight:500;color:#222;display:block}
.member p{font-size:11.5px;color:#444;margin-top:4px;line-height:1.3}
.btn-orange{background:var(--orange)}
.btn-navy{background:var(--navy)}
.btn-team{top:1122px;height:36px;width:240px;font-size:15px}

/* about */
.about{left:0;top:1200px;width:1200px;height:705px;background:linear-gradient(180deg,#24367a,#1d2b68);clip-path:polygon(0 8%,100% 0,100% 93%,0 100%)}
.about-text{left:230px;top:1312px;width:740px;color:#fff;font-size:12px;line-height:1.55;text-align:center}
.slide-band{left:120px;top:1468px;width:958px;height:244px;background:var(--orange)}
.slide-card{left:280px;top:1438px;width:637px;height:307px;background:linear-gradient(180deg,#fafafa,#ececec);box-shadow:0 4px 14px rgba(0,0,0,.35)}
.slide-arrow{width:32px;height:32px;border-radius:50%;background:#fff;display:flex;align-items:center;justify-content:center;box-shadow:0 1px 4px rgba(0,0,0,.3)}
.cta{left:0;top:1772px;width:1200px;display:flex;justify-content:center;align-items:center;gap:22px;color:#fff;font-size:24px;font-weight:300}
.cta .btn{width:114px;height:38px;background:var(--navy-deep);border:1px solid #5d6fb3;font-size:14px}

/* services */
.services-text{left:215px;top:1960px;width:770px;font-size:12px;line-height:1.6;text-align:center;color:#333}
.cards{left:162px;top:2115px;display:flex;gap:0}
.card{width:292px;height:280px;background:var(--panel);border-top:8px solid var(--navy);box-shadow:0 2px 6px rgba(0,0,0,.25);position:relative;text-align:center;padding:30px 36px 0}
.card.mid{border-top-color:var(--orange);background:#fafafa}
.card h4{font-size:14px;font-weight:700;margin-top:14px;color:#222}
.card p{font-size:12px;line-height:1.5;color:#444;margin-top:12px}
.card .plus{position:absolute;left:129px;bottom:-16px;width:34px;height:34px;border-radius:50%;background:var(--navy);color:#fff;font-size:22px;display:flex;align-items:center;justify-content:center}
.card.mid .plus{background:var(--orange)}

/* steps */
.steps-bg{left:0;top:2430px;width:1200px;height:660px;background:var(--grey);clip-path:polygon(0 0,100% 4%,100% 100%,0 100%)}
.tabs{left:140px;top:2596px;width:288px;background:#e3e3e3}
.tab{height:56px;display:flex;align-items:center;padding-left:36px;font-size:12.5px;color:#333;border-bottom:1px solid #fff;background:#f6f6f6}
.tab.on{background:var(--orange);color:#fff}
.panel{left:434px;top:2587px;width:630px;height:440px;background:#fff;box-shadow:0 2px 8px rgba(0,0,0,.2);padding:22px 22px;font-size:11px;line-height:1.5;color:#333}
.panel h5{font-size:16px;font-weight:400;color:var(--navy)}
.panel h5 span{color:var(--orange)}
.panel h6{font-size:10.5px;font-weight:700;color:var(--orange);margin:10px 0 8px}
.panel p{margin-bottom:8px}
.panel .note{font-style:italic;font-size:10.5px}

/* blueprint */
.blueprint{left:0;top:3077px;width:1200px;height:391px;background:linear-gradient(180deg,#c9c8c4,#dcd6ca 50%,#bfb39a);clip-path:polygon(0 0,100% 14%,100% 100%,0 100%)}
.blueprint-title{left:0;top:3264px;width:1200px;text-align:center;font-size:27px;font-weight:700;color:#1b1b1b;line-height:1.3}

/* contact */
.contact-intro{left:200px;top:3598px;width:800px;text-align:center;font-size:13.5px;line-height:1.45;color:#222}
.contact-intro em{font-style:normal;color:var(--orange)}
.info{left:252px;top:3735px;width:260px;font-size:11.5px;color:#222}
.info h4{font-size:18px;font-weight:500;margin-bottom:22px}
.info li{list-style:none;display:flex;align-items:center;gap:20px;margin-bottom:12px;font-weight:500}
.info .marks{display:flex;gap:12px;margin-top:10px}
.info .marks span{display:block;height:22px;border-radius:2px}
.info .social{margin-top:22px}
.info .social span{width:28px;height:28px}
.form{left:551px;top:3740px;width:395px}
.field{background:#e8e8e8;height:38px;font-size:11px;color:#555;padding:10px 12px;margin-bottom:14px}
.row{display:flex;gap:10px}
.row .field{flex:1}
.field.msg{height:64px}
.btn-submit{left:551px;top:3924px;width:115px;height:36px;background:var(--navy);font-size:15px}

/* footer */
.footer{left:0;top:3986px;width:1200px;height:210px;background:#252525}
.footer nav{left:0;top:58px;width:1200px;display:flex;justify-content:center;gap:40px;color:#fff;font-size:15px}
.footer .mark{left:0;top:100px;width:1200px;text-align:center;color:#fff;font-weight:900;font-size:28px;letter-spacing:2px}
.footer .copy{left:0;top:173px;width:1200px;text-align:center;color:#ccc;font-size:11px}
.to-top{left:1040px;top:3990px;width:40px;height:40px;border-radius:50%;background:#fff;box-shadow:0 1px 5px rgba(0,0,0,.3);display:flex;align-items:center;justify-content:center}
</style>
</head>
<body>

<!-- header -->
<div class="abs topbar">
  <div class="abs call">
    <small><svg width="14" height="14" viewBox="0 0 24 24"><path fill="#fff" d="M6.6 10.8a15 15 0 006.6 6.6l2.2-2.2c.3-.3.7-.4 1-.2 1.1.4 2.3.6 3.6.6.6 0 1 .4 1 1V20c0 .6-.4 1-1 1A17 17 0 013 4c0-.6.4-1 1-1h3.5c.6 0 1 .4 1 1 0 1.3.2 2.5.6 3.6.1.3 0 .7-.2 1z"/></svg>Call Us</small>
    <strong>(855) 555 0142</strong>
  </div>
</div>
<div class="abs navbar">
  <nav class="abs nav"><a>Home</a><a>About</a><a>Work</a><a>Services</a><a>Contact Us</a></nav>
  <div class="abs social blue"><span></span><span></span><span></span><span></span></div>
</div>
<div class="abs brand-badge">BROVIK</div>

<!-- hero -->
<div class="abs hero" role="img" aria-label="Roofer installing shingles on a residential roof"></div>
<div class="abs arrow-circle" style="left:100px;top:373px"><svg width="14" height="14" viewBox="0 0 14 14"><path d="M9 2L4 7l5 5" stroke="#333" stroke-width="2" fill="none"/></svg></div>
<div class="abs arrow-circle" style="left:1058px;top:373px"><svg width="14" height="14" viewBox="0 0 14 14"><path d="M5 2l5 5-5 5" stroke="#333" stroke-width="2" fill="none"/></svg></div>
<div class="abs hero-copy">
  <h1>BROVIK CONTRACTING</h1>
  <h2>OUR MISSION</h2>
  <p>Brovik Contracting takes a Lifetime Relationship approach to solving all our client's construction contracting needs. We believe in leveraging our knowledge with our network to deliver optimal value for our client's properties.</p>
</div>
<a class="abs btn btn-learn">LEARN MORE</a>
<div class="abs badges"><span style="width:104px"></span><span style="width:40px;border-radius:50%"></span><span style="width:104px"></span></div>
<div class="abs side-tab">
  <svg class="abs" style="left:13px;top:14px" width="18" height="18" viewBox="0 0 24 24"><path fill="#fff" d="M6.6 10.8a15 15 0 006.6 6.6l2.2-2.2c.3-.3.7-.4 1-.2 1.1.4 2.3.6 3.6.6.6 0 1 .4 1 1V20c0 .6-.4 1-1 1A17 17 0 013 4c0-.6.4-1 1-1h3.5c.6 0 1 .4 1 1 0 1.3.2 2.5.6 3.6.1.3 0 .7-.2 1z"/></svg>
  <span>Contact Us</span>
</div>

<!-- our work -->
<h2 class="abs title" style="top:684px">OUR WORK</h2>
<div class="abs video" role="img" aria-label="Video still of a shingled roof seen from above"></div>
<div class="abs play"><svg width="22" height="24" viewBox="0 0 22 24"><path d="M2 1l19 11L2 23z" fill="#fff"/></svg></div>
<div class="abs team">
  <h3>Our Team</h3>
  <div class="member"><div class="ico on"><svg width="22" height="22" viewBox="0 0 24 24"><path d="M4 20C4 10 10 4 20 4c0 10-6 16-16 16zM4 20l9-9" stroke="#fff" stroke-width="2" fill="none"/></svg></div><div><b>Green Energy Consultants</b><p>Our Green energy consultants find you tax incentives and quantify the added value to your property from implementing green energy.</p></div></div>
  <div class="member"><div class="ico"><svg width="20" height="22" viewBox="0 0 20 22"><rect x="3" y="2" width="14" height="18" stroke="#999" stroke-width="1.5" fill="none"/><path d="M6 7h8M6 11h8M6 15h5" stroke="#999" stroke-width="1.5"/></svg></div><div><b>Building Code Experts</b><p>We ALWAYS follow the most recent building codes!</p></div></div>
  <div class="member"><div class="ico"><svg width="22" height="22" viewBox="0 0 22 22"><circle cx="11" cy="7" r="4" stroke="#999" stroke-width="1.5" fill="none"/><path d="M3 20c1-5 5-7 8-7s7 2 8 7" stroke="#999" stroke-width="1.5" fill="none"/></svg></div><div><b>Designers, Architects, and Decorators</b><p>Our design professionals help you bring your dream home to life!</p></div></div>
  <div class="member"><div class="ico"><svg width="22" height="22" viewBox="0 0 22 22"><circle cx="11" cy="7" r="4" stroke="#999" stroke-width="1.5" fill="none"/><path d="M3 20c1-5 5-7 8-7s7 2 8 7" stroke="#999" stroke-width="1.5" fill="none"/></svg></div><div><b>Engineers, Public Adjusters and Appraisers</b><p>Assist in the claims process to make sure no money is left on the table.</p></div></div>
</div>
<a class="abs btn btn-orange btn-team" style="left:361px">Who Does Our Team Serve?</a>
<a class="abs btn btn-navy btn-team" style="left:626px">How Do YOU Benefit?</a>

<!-- about -->
<div class="abs about" role="img" aria-label="Dusk view of a two-storey brick home behind a blue overlay"></div>
<h2 class="abs" style="left:0;top:1258px;width:1200px;text-align:center;color:#fff;font-size:27px;font-weight:700">ABOUT</h2>
<p class="abs about-text">Brovik Contracting takes a customer oriented approach to solving all of our client's needs. Realizing that no two projects are ever the same, Brovik Contracting uses forward thinking techniques to satisfy our customers. While most contracting companies use construction methods that are over half of a century old, Brovik Contracting sets the bar in innovative thinking. With our team of certified adjusters, we work hand in hand with our customers to provide unprecedented customer service and the utmost efficiency.</p>
<div class="abs slide-band"></div>
<div class="abs slide-card" role="img" aria-label="Promotional slide for premium house painting services with paint brand partners"></div>
<div class="abs slide-arrow" style="left:254px;top:1560px"><svg width="12" height="12" viewBox="0 0 14 14"><path d="M9 2L4 7l5 5" stroke="#333" stroke-width="2" fill="none"/></svg></div>
<div class="abs slide-arrow" style="left:912px;top:1560px"><svg width="12" height="12" viewBox="0 0 14 14"><path d="M5 2l5 5-5 5" stroke="#333" stroke-width="2" fill="none"/></svg></div>
<div class="abs cta"><span>What can Brovik Contracting do for you?</span><a class="btn">Contact Us</a></div>

<!-- services -->
<h2 class="abs title" style="top:1910px">SERVICES</h2>
<p class="abs services-text">Brovik Contracting provides professional services for our customers' homes. We work with you to assess your specific needs and guarantee you a custom solution. Although we specialize in insurance claims, our experts offer a wide range of services with customized service to ensure you get exactly what you need when you need it. In addition to roof repair and installation we offer a preventive maintenance program entitled the Roof Quality Preservation Program. This program includes roof and gutter cleaning as well as a complimentary inspection for any roof or gutter damage. Below you will find an assortment of services we offer homeowners.</p>
<svg class="abs" style="left:126px;top:2234px" width="14" height="18" viewBox="0 0 14 18"><path d="M10 2L3 9l7 7" stroke="#333" stroke-width="2.5" fill="none"/></svg>
<svg class="abs" style="left:1066px;top:2234px" width="14" height="18" viewBox="0 0 14 18"><path d="M4 2l7 7-7 7" stroke="#333" stroke-width="2.5" fill="none"/></svg>
<div class="abs cards">
  <div class="card"><svg width="82" height="42" viewBox="0 0 82 42"><path d="M4 38L41 6l37 32" stroke="var(--navy)" stroke-width="6" fill="none"/><rect x="58" y="6" width="8" height="16" fill="var(--navy)"/></svg><h4>ROOFING</h4><p>One of the most important parts of your home is the roof. Your roof protects your home from the elements, helps regulate the inside temperature, and may help lower your energy costs.</p><span class="plus">+</span></div>
  <div class="card mid"><svg width="66" height="48" viewBox="0 0 66 48"><path d="M4 16L62 4M4 28L62 16M4 40L62 28M4 48L62 40" stroke="var(--orange)" stroke-width="8"/></svg><h4>SIDING</h4><p>Old, deteriorating, or damaged siding can leave your house looking incomplete and can pose just as much of a problem as a leaking roof.</p><span class="plus">+</span></div>
  <div class="card"><svg width="60" height="50" viewBox="0 0 60 50"><path d="M8 6v30c0 6 4 10 10 10h24c6 0 10-4 10-10V20" stroke="var(--navy)" stroke-width="6" fill="none"/><path d="M20 4v22M32 12v14" stroke="var(--navy)" stroke-width="6"/></svg><h4>GUTTERS</h4><p>By diverting water from the base of the building, rain gutters help guard against erosion, leaks, foundation damage, and other serious problems.</p><span class="plus">+</span></div>
</div>

<!-- steps -->
<div class="abs steps-bg"></div>
<h2 class="abs title" style="top:2504px">A STEP-BY-STEP GUIDE TO SUCCESSFUL HOME REPAIR</h2>
<div class="abs tabs">
  <div class="tab on">THE INSPECTION PROCESS</div>
  <div class="tab">PRE CONSTRUCTION</div>
  <div class="tab">PAYMENT INFORMATION</div>
  <div class="tab">CONSTRUCTION DAY AND FINAL PAYMENT</div>
  <div class="tab">POST CONSTRUCTION</div>
</div>
<div class="abs panel">
  <h5>STEP 1: <span>INSPECTION</span></h5>
  <h6>A CONSTRUCTION CONSULTANT WILL INSPECT YOUR PROPERTY FOR SIGNS OF DAMAGE.</h6>
  <p>We use the same inspection and estimating software as most insurance providers. An inspection from Brovik Contracting includes site visits and photography by a friendly and knowledgeable Construction Consultant.</p>
  <p>The site visit and photographs are documented and included in the Findings Report.</p>
  <h5 style="margin-top:14px">STEP 2: <span>FINDINGS REPORT AND LETTER OF INTENT</span></h5>
  <h6>THE CONSTRUCTION CONSULTANT WILL NOTIFY YOU OF ITS FINDINGS.</h6>
  <p>After the initial inspection, our Construction Consultant will notify you of any damage discovered and give you a personalized Findings Report.</p>
  <p>If extensive damage is discovered during the inspection, a Letter of Intent along with an Insurance Claim should promptly be filed.</p>
  <p>The Letter of Intent binds the Customer and Brovik Contracting to an agreement allowing Brovik Contracting to further inspect, estimate and setup for the project.</p>
  <p class="note">Note: As a homeowner, you have a contractual duty to your insurance company to inspect and take care of your property in order to mitigate unnecessary damages. Once you are aware of damage to your home, most insurance policies only allow you 365 days to file a claim or you forfeit your right to obtain payment from the insurance company.</p>
</div>

<!-- blueprint -->
<div class="abs blueprint" role="img" aria-label="Wooden house frame model resting on rolled architectural plans"></div>
<h2 class="abs blueprint-title">BROVIK CONTRACTING OFFERS YOU THE BLUEPRINT<br>TO SUCCESSFUL ROOF AND HOME REPAIRS.</h2>

<!-- contact -->
<h2 class="abs title" style="top:3543px">CONTACT</h2>
<p class="abs contact-intro">Thank you for visiting our website. For questions, comments, or suggestions please fill out the form below. To schedule a free inspection call us directly at <em>(855) 555-0142</em>.<br><br>-Best Regards<br>The Brovik Contracting Team.</p>
<div class="abs info">
  <h4>Contact Info</h4>
  <ul>
    <li><svg width="12" height="12" viewBox="0 0 24 24"><path fill="#333" d="M6.6 10.8a15 15 0 006.6 6.6l2.2-2.2c.3-.3.7-.4 1-.2 1.1.4 2.3.6 3.6.6.6 0 1 .4 1 1V20c0 .6-.4 1-1 1A17 17 0 013 4c0-.6.4-1 1-1h3.5c.6 0 1 .4 1 1 0 1.3.2 2.5.6 3.6.1.3 0 .7-.2 1z"/></svg>(855) 555-0142</li>
    <li><svg width="13" height="10" viewBox="0 0 13 10"><rect x=".5" y=".5" width="12" height="9" stroke="#333" fill="none"/><path d="M.5 .5l6 5 6-5" stroke="#333" fill="none"/></svg>info@brovikbuilders.com</li>
    <li><svg width="10" height="14" viewBox="0 0 10 14"><path d="M5 0a5 5 0 00-5 5c0 4 5 9 5 9s5-5 5-9a5 5 0 00-5-5zm0 7a2 2 0 110-4 2 2 0 010 4z" fill="#333"/></svg>412 Mill St. Carver, TX 75010</li>
  </ul>
  <div class="marks"><span style="width:66px;background:var(--navy)"></span><span style="width:48px;background:#d32323"></span></div>
  <div class="social blue"><span></span><span></span><span></span><span></span></div>
</div>
<div class="abs form">
  <div class="row"><div class="field">First Name</div><div class="field">Last Name</div></div>
  <div class="row"><div class="field">Email</div><div class="field">Phone</div></div>
  <div class="field msg">Message</div>
</div>
<a class="abs btn btn-submit">Submit</a>

<!-- footer -->
<div class="abs footer">
  <nav class="abs"><a>Home</a><a>About</a><a>Work</a><a>Services</a><a>Contact Us</a></nav>
  <div class="abs mark">BROVIK</div>
  <p class="abs copy">© Brovik Contracting ©2017 . All Rights Reserved.</p>
</div>
<div class="abs to-top"><svg width="14" height="10" viewBox="0 0 14 10"><path d="M2 8l5-5 5 5" stroke="#333" stroke-width="2" fill="none"/></svg></div>

</body>
</html>
```